Veltrana Capital LLC

Need Professional Business cards for New Investment Fund

Target Market(s)

High Quality investors

Industry/Entity Type

Financial

Contact Information for Business Card

Phone Number +1 555 284 6190
Name Lukas Varenko
Title Fund Manager
email lv@FundVeltrana.com
Website www.FundVeltrana.com

Colors

Designer to choose colors to be used in the design.

Requirements
Must have
• Must have our Logo and all of the above. Must be made so lettering and loge can be raised

```html
<!DOCTYPE html>
<html lang="en">
<head>
<meta charset="utf-8">
<title>Veltrana Capital — Business Card</title>
<link rel="stylesheet" href="https://fonts.googleapis.com/css2?family=Didact+Gothic&family=Poppins:wght@600&display=swap">
<style>
  :root {
    --page: #ececec;
    --card: #434f42;
    --accent: #1ee60a;
    --ink: #ffffff;
  }
  * { margin: 0; padding: 0; box-sizing: border-box; }
  html, body { width: 1200px; height: 1028px; overflow: hidden; }
  body { background: var(--page); position: relative; font-family: "Didact Gothic", sans-serif; }

  .card {
    position: absolute;
    left: 310px;
    width: 578px;
    height: 330px;
    background: var(--card);
    border-radius: 26px;
    overflow: hidden;
  }
  .card--front { top: 165px; }
  .card--back { top: 532px; display: flex; align-items: center; justify-content: center; }

  .holder-name {
    position: absolute; left: 31px; top: 96px;
    font-family: "Poppins", sans-serif; font-weight: 600;
    font-size: 21px; line-height: 1; color: var(--accent); letter-spacing: 0.3px;
  }
  .holder-title {
    position: absolute; left: 31px; top: 120px;
    font-size: 16.5px; line-height: 1; color: var(--ink); letter-spacing: 0.2px;
  }
  .divider {
    position: absolute; left: 31px; top: 162px;
    width: 340px; height: 5px; background: var(--accent);
  }
  .contact-list {
    position: absolute; left: 31px; top: 189px;
    list-style: none;
  }
  .contact-list li {
    display: flex; align-items: center; gap: 9px;
    height: 21px; font-size: 16px; line-height: 1; color: var(--ink); letter-spacing: 0.3px;
  }
  .contact-list svg { width: 11px; height: 11px; flex: none; }

  .brand { display: flex; align-items: center; gap: 10px; }
  .brand-mark { width: 20px; height: 20px; background: var(--accent); flex: none; }
  .brand-name {
    font-family: "Poppins", sans-serif; font-weight: 600;
    font-size: 23px; color: var(--ink); letter-spacing: 1px; line-height: 1;
  }
  .card--front .brand { position: absolute; left: 384px; top: 153px; }
</style>
</head>
<body>
  <section class="card card--front">
    <h1 class="holder-name">Lukas Varenko</h1>
    <p class="holder-title">Fund Manager</p>
    <div class="divider"></div>
    <ul class="contact-list">
      <li>
        <svg viewBox="0 0 12 12" aria-hidden="true"><path d="M3 1 L5 3.5 L4 5 Q5.5 7.5 7 8 L8.5 7 L11 9 L10 11 Q4 11 1 2 Z" fill="none" stroke="var(--accent)" stroke-width="1.2"/></svg>
        +1 555 284 6190
      </li>
      <li>
        <svg viewBox="0 0 12 12" aria-hidden="true"><rect x="1" y="2.5" width="10" height="7" fill="none" stroke="var(--accent)" stroke-width="1.2"/><path d="M1 3 L6 7 L11 3" fill="none" stroke="var(--accent)" stroke-width="1.2"/></svg>
        lv@FundVeltrana.com
      </li>
      <li>
        <svg viewBox="0 0 12 12" aria-hidden="true"><circle cx="6" cy="6" r="5" fill="none" stroke="var(--accent)" stroke-width="1.2"/><ellipse cx="6" cy="6" rx="2.2" ry="5" fill="none" stroke="var(--accent)" stroke-width="1"/><path d="M1 6 H11" stroke="var(--accent)" stroke-width="1"/></svg>
        www.FundVeltrana.com
      </li>
    </ul>
    <div class="brand">
      <span class="brand-mark"></span>
      <span class="brand-name">VELTRANA</span>
    </div>
  </section>

  <section class="card card--back">
    <div class="brand">
      <span class="brand-mark"></span>
      <span class="brand-name">VELTRANA</span>
    </div>
  </section>
</body>
</html>
```